Need Help having my business card stand out

I am the owner of Birchway Canine Training and would like for my business cards to stand out. I have been trying to keep designing them myself but I can't get what I have in my head on the card. I will try my best to post templates that I like for inspirations. I want something unique but elegant. I don't want in to look cartoony or cheesy. It needs to pop in a pet shop but also in a coffee shop or gym.

Target Market(s)

Dog owners, Married ,No young kids Jr High school kids and up (maybe kids on the way) Executives, Stay at home moms/wives, Small business owners

Industry/Entity Type

Dog Training

Contact Information for Business Card

Lowell Spratt, 281-904-3376, info@birchwaycanine.example, www.birchwaycanine.example

Colors

Designer to choose colors to be used in the design.

Requirements
Must have
• my logo
Should not have
• Cursive lettering

```html
<!DOCTYPE html>
<html lang="en">
<head>
<meta charset="utf-8">
<title>Birchway Canine Training — Business Card</title>
<link href="https://fonts.googleapis.com/css2?family=Open+Sans:wght@400;600;700&display=swap" rel="stylesheet">
<style>
  :root {
    --stage: #d4d4d4;
    --peach: #fbefe7;
    --stripe: #f6e0d3;
    --maroon: #5b1d1f;
    --tan: #b88664;
    --tan-dark: #a87453;
    --photo-light: #fbfbfa;
    --photo-mid: #ecebe8;
    --strip: rgba(235, 232, 228, 0.85);
    --white: #ffffff;
  }
  * { margin: 0; padding: 0; box-sizing: border-box; }
  html, body { width: 1200px; height: 800px; overflow: hidden; }
  body {
    background: var(--stage);
    font-family: "Open Sans", Arial, sans-serif;
    position: relative;
  }
  .card {
    position: absolute;
    top: 240px;
    width: 560px;
    height: 320px;
    overflow: hidden;
    box-shadow: 0 6px 18px rgba(0,0,0,0.12);
  }
  .card--front { left: 20px; }
  .card--back { left: 620px; }

  /* Front */
  .front__photo {
    position: absolute; inset: 0;
    background: radial-gradient(ellipse at 45% 55%, var(--photo-mid) 0%, var(--photo-light) 60%, var(--white) 100%);
  }
  .brand {
    position: absolute;
    display: flex; align-items: center; gap: 10px;
    color: var(--maroon);
    font-weight: 700;
    white-space: nowrap;
  }
  .brand__rule { display: block; height: 1.5px; background: var(--tan); }
  .front__brand { top: 26px; right: 22px; font-size: 15px; }
  .front__brand .brand__rule { width: 22px; }
  .front__strip {
    position: absolute; left: 200px; right: 0; bottom: 18px; height: 36px;
    background: var(--strip);
    display: flex; align-items: center; justify-content: flex-end;
    padding-right: 24px;
    color: var(--maroon);
    font-weight: 700; font-size: 15px; letter-spacing: 1.5px;
    text-transform: uppercase;
  }

  /* Back */
  .card--back {
    background-color: var(--peach);
    background-image: repeating-linear-gradient(-50deg, var(--stripe) 0 1.5px, transparent 1.5px 7px);
  }
  .back__shapes { position: absolute; inset: 0; }
  .back__brand {
    top: 48px; left: 0; right: 0; justify-content: center;
    font-size: 23px;
  }
  .back__brand .brand__rule { width: 34px; }
  .back__owner {
    position: absolute; top: 96px; left: 0; right: 0;
    text-align: center;
    color: var(--tan-dark);
    font-size: 13px; font-weight: 600;
    letter-spacing: 2px;
    text-transform: uppercase;
  }
  .back__address {
    position: absolute; top: 134px; left: 0; right: 0;
    text-align: center;
    color: var(--maroon);
    font-size: 15px;
  }
  .back__online {
    position: absolute; top: 210px; left: 162px; right: 16px;
    display: flex; justify-content: space-between; align-items: center;
    color: var(--tan-dark);
    font-size: 11.5px;
    white-space: nowrap;
  }
  .back__online .web { font-weight: 700; }
  .back__phone {
    position: absolute; top: 258px; left: 162px;
    display: flex; gap: 8px; align-items: center;
    color: var(--white);
    font-size: 13px; font-weight: 600;
  }
  .contact-item { display: flex; align-items: center; gap: 6px; }
  .icon { width: 14px; height: 14px; flex: none; }
</style>
</head>
<body>

  <section class="card card--front" aria-label="Business card front">
    <div class="front__photo" role="img" aria-label="Photograph of a white fluffy puppy raising its paws"></div>
    <div class="brand front__brand">
      <span class="brand__rule"></span>
      <span class="brand__name">Birchway Canine Training</span>
      <span class="brand__rule"></span>
    </div>
    <div class="front__strip">Your Dog Trainer for Life</div>
  </section>

  <section class="card card--back" aria-label="Business card back">
    <svg class="back__shapes" width="560" height="320" viewBox="0 0 560 320" aria-hidden="true">
      <defs>
        <linearGradient id="bandTone" x1="0" y1="0" x2="1" y2="0">
          <stop offset="0" stop-color="#b07b58"/>
          <stop offset="0.5" stop-color="#c29574"/>
          <stop offset="1" stop-color="#b38060"/>
        </linearGradient>
      </defs>
      <path class="top-tab" d="M180 0 H390 V10 Q390 20 380 20 H190 Q180 20 180 10 Z" fill="url(#bandTone)"/>
      <path class="bottom-band" d="M0 196 H138 Q150 196 150 208 V228 Q150 240 162 240 H560 V320 H0 Z" fill="url(#bandTone)"/>
    </svg>

    <div class="brand back__brand">
      <span class="brand__rule"></span>
      <span class="brand__name">Birchway Canine Training</span>
      <span class="brand__rule"></span>
    </div>

    <p class="back__owner">Lowell Spratt</p>

    <p class="back__address">000 Birch Lane, Suite 300, Hollis, US 0000</p>

    <div class="back__online">
      <span class="web">www.birchwaycanine.example</span>
      <span class="contact-item">
        <svg class="icon" viewBox="0 0 16 16" aria-hidden="true"><circle cx="8" cy="8" r="8" fill="#a87453"/><rect x="4" y="5" width="8" height="6" rx="1" fill="#fbefe7"/><path d="M4 5.5 L8 8.5 L12 5.5" stroke="#a87453" stroke-width="1" fill="none"/></svg>
        info@birchwaycanine.example
      </span>
    </div>

    <div class="back__phone">
      <svg class="icon" viewBox="0 0 16 16" aria-hidden="true"><circle cx="8" cy="8" r="7.3" fill="none" stroke="#ffffff" stroke-width="1.2"/><path d="M5.5 4.5 Q4.5 5 5 6.8 Q6 9.5 9 11 Q10.8 11.7 11.4 10.6 L10.2 9.4 L9.2 9.9 Q7.4 9 6.3 7 L6.8 5.9 Z" fill="#ffffff"/></svg>
      <span>281-904-3376</span>
    </div>
  </section>

</body>
</html>
```